Brookvale Estates LLC stationary for a real estate property management company.

Create stationary (letterhead, envelopes, business cards) using Brookvale Estates LLC logo as primary creative element. Stationary design needs to be horizontal, leaving as much space as possible for correspondence copy. See attached Creative Brief and past stationary files for details.

Target Market(s)

Prospective apartment residents and current residents, vendors, and government agencies.

Industry/Entity Type

Property Management

Contact Information for Business Card

Business card employee title: Property Manager. Should include address, phone, fax, email, website, slogan, and Brookvale Estates logo.

Font styles to use
Sans Serif

Colors
0592cd
000000

Requirements
Must have
• Tone should be conservative, institutional, business (i.e. banking, finance, real estate). Must include: address, phone, fax, website, and slogan (see attached Creative Brief). Should be a horizontal design, leaving as much room as possible for letter correspondence copy.
Nice to have
• Please use an Arial or Helvetica style font.
Should not have
• Letterhead layout should leave as much room as possible for copy.

```html
<!DOCTYPE html>
<html lang="en">
<head>
<meta charset="utf-8">
<title>Brookvale Estates LLC – Business Card</title>
<link rel="stylesheet" href="https://fonts.googleapis.com/css2?family=Arimo:wght@400;700&display=swap">
<style>
  :root {
    --backdrop: #2b2b2b;
    --paper: #f6f6f6;
    --brand-blue: #0a6ea8;
    --band-top: #1a9ad6;
    --band-bottom: #0b64a0;
    --rule: #4a4a4a;
    --slogan-grey: #4d4d4d;
    --reverse-light: #6d6d70;
    --reverse-dark: #3c3c3e;
    --white: #ffffff;
  }
  * { box-sizing: border-box; margin: 0; padding: 0; }
  html, body { width: 1200px; height: 960px; overflow: hidden; }
  body {
    background: var(--backdrop);
    font-family: "Arimo", Arial, Helvetica, sans-serif;
    position: relative;
  }
  .card {
    position: absolute;
    width: 600px;
    height: 342px;
    overflow: hidden;
  }
  /* Front */
  .card-front { left: 302px; top: 129px; background: var(--paper); }
  .brand-block {
    position: absolute;
    right: 40px;
    top: 66px;
    text-align: right;
  }
  .brand-name {
    display: flex;
    align-items: center;
    justify-content: flex-end;
    gap: 10px;
    color: var(--brand-blue);
    font-weight: 700;
    font-size: 25px;
    letter-spacing: 0.5px;
  }
  .brand-mark {
    width: 16px; height: 16px;
    background: var(--brand-blue);
  }
  .brand-slogan {
    margin-top: 12px;
    font-size: 14.5px;
    color: var(--slogan-grey);
    letter-spacing: 0.4px;
  }
  .divider {
    position: absolute;
    left: 0; right: 0;
    top: 189px;
    height: 4px;
    background: var(--rule);
  }
  .contact-band {
    position: absolute;
    left: 0; right: 0;
    top: 193px; bottom: 0;
    background: linear-gradient(160deg, var(--band-top), var(--band-bottom));
    color: var(--white);
  }
  .person {
    position: absolute;
    left: 33px;
    top: 34px;
  }
  .person-name { font-weight: 700; font-size: 21px; }
  .person-title { font-size: 15px; margin-top: 2px; }
  .person-address { font-size: 14px; line-height: 20px; margin-top: 14px; }
  .contact-list {
    position: absolute;
    right: 34px;
    top: 40px;
    list-style: none;
    font-size: 14px;
    line-height: 19.5px;
    letter-spacing: 0.3px;
  }
  .contact-list li {
    display: flex;
    align-items: center;
    justify-content: flex-end;
    gap: 10px;
  }
  .contact-list svg { width: 14px; height: 14px; fill: var(--white); }
  /* Back */
  .card-back {
    left: 299px; top: 489px;
    background: linear-gradient(135deg, var(--reverse-light) 0%, var(--reverse-dark) 55%, var(--reverse-dark) 100%);
    color: var(--white);
    text-align: center;
  }
  .reverse-name {
    position: absolute;
    left: 0; right: 0;
    top: 140px;
    font-weight: 700;
    font-size: 30px;
    letter-spacing: 1px;
  }
  .reverse-slogan {
    position: absolute;
    left: 0; right: 0;
    top: 288px;
    font-weight: 700;
    font-size: 16.5px;
  }
</style>
</head>
<body>
  <section class="card card-front">
    <div class="brand-block">
      <div class="brand-name"><span class="brand-mark"></span>BROOKVALE ESTATES LLC</div>
      <div class="brand-slogan">Multifamily Property Management</div>
    </div>
    <div class="divider"></div>
    <div class="contact-band">
      <div class="person">
        <div class="person-name">DANA WHITFIELD</div>
        <div class="person-title">Property Manager</div>
        <div class="person-address">2760 Alder Creek Road #B210<br>Fresno, CA 93722</div>
      </div>
      <ul class="contact-list">
        <li>559-304-7718
          <svg viewBox="0 0 16 16" aria-label="Phone"><path d="M3.6 1.2l2.3 2.6-1.2 1.7c.9 2 2.4 3.6 4.4 4.6l1.7-1.2 2.6 2.3-1.5 2.2C7.4 13.5 2.4 8.4 1.5 3z"/></svg></li>
        <li>559-304-7719
          <svg viewBox="0 0 16 16" aria-label="Fax"><rect x="4" y="1" width="8" height="4"/><rect x="1" y="6" width="14" height="6" rx="1"/><rect x="4" y="10" width="8" height="5" fill="#0b64a0"/><rect x="5" y="11" width="6" height="3"/></svg></li>
        <li>dana@brookvaleestates.us
          <svg viewBox="0 0 16 16" aria-label="Email"><rect x="1" y="3" width="14" height="10"/><path d="M1 3l7 6 7-6" fill="none" stroke="#0b64a0" stroke-width="1.4"/></svg></li>
        <li>www.brookvaleestates.us
          <svg viewBox="0 0 16 16" aria-label="Website"><circle cx="8" cy="8" r="7"/><path d="M1 8h14M8 1c-3 3.5-3 10.5 0 14M8 1c3 3.5 3 10.5 0 14" fill="none" stroke="#0b64a0" stroke-width="1.1"/></svg></li>
      </ul>
    </div>
  </section>

  <section class="card card-back">
    <div class="reverse-name">BROOKVALE ESTATES LLC</div>
    <div class="reverse-slogan">Multifamily Property Management</div>
  </section>
</body>
</html>
```